Business Card for premium dental clinic

We are a premium dental clinic based in Brasov, Romania with more than 15 year on the market, providing quality dental treatment made by a team of more specialized dentists, working with modern equipment as a solution to beautiful and healthy teeth.

Our current logo for the clinic use 2 square with colors black and gold - dr Ternisu - studio, using family fonts Bodoni, Myriad Pro and Segoe Print.
Depending on the printing we used some gold CMYK background or gold foil picture background or a gold gradient.
We want a business card:
- eye catching business card
- distinguished business card
- premium design
- to keep the color scheme of black and gold
- to attract the customers to spent time reading the information
- modern concept

```html
<!DOCTYPE html>
<html lang="en">
<head>
<meta charset="utf-8">
<title>dr Ternisu – Business Card</title>
<link href="https://fonts.googleapis.com/css2?family=Roboto:wght@400;500;700&display=swap" rel="stylesheet">
<style>
  :root{
    --backdrop:#9a9a9a;
    --paper:#f6f6f4;
    --gold:#e7b21c;
    --gold-light:#f6d45a;
    --gold-edge:#c98a12;
    --ink:#1f1f1f;
    --grey:#6e6e6e;
  }
  html,body{margin:0;padding:0;overflow:hidden}
  body{width:1200px;height:1059px;background:var(--backdrop);font-family:'Roboto',Arial,sans-serif;position:relative}
  .card{position:absolute;left:250px;width:700px;height:400px;background:var(--paper);
    border-bottom:4px solid var(--gold-edge);box-shadow:0 12px 30px rgba(0,0,0,.25)}
  .card--front{top:70px}
  .card--back{top:560px}
  .brand{position:absolute;display:flex;align-items:center;gap:14px}
  .card--front .brand{left:48px;top:168px}
  .card--back .brand{left:50%;top:50%;transform:translate(-50%,-50%)}
  .brand__square{width:46px;height:46px;background:var(--gold)}
  .brand__name{font-size:40px;font-weight:400;color:var(--ink);letter-spacing:.5px}
  .contact{position:absolute;left:400px;top:96px;color:var(--grey)}
  .contact__name{font-size:30px;font-weight:700;color:var(--gold);margin:0;letter-spacing:1px}
  .contact__role{font-size:17px;font-weight:500;color:var(--ink);margin:2px 0 20px}
  .contact__address{font-size:18px;line-height:24px;margin:0 0 18px}
  .contact__list{list-style:none;margin:0;padding:0;font-size:18px;line-height:27px}
  .contact__list li{display:flex;align-items:center;gap:10px}
  .contact__list svg{width:14px;height:14px;fill:var(--gold)}
</style>
</head>
<body>
  <section class="card card--front">
    <div class="brand">
      <span class="brand__square"></span>
      <span class="brand__name">dr Ternisu</span>
    </div>
    <div class="contact">
      <p class="contact__name">Andrei Morovan</p>
      <p class="contact__role">President</p>
      <p class="contact__address">412 Linden Street<br>Brasov, Romania 500123</p>
      <ul class="contact__list">
        <li><svg viewBox="0 0 16 16"><path d="M3 1l3 3-2 2c1 2 3 4 5 5l2-2 3 3-2 3C7 15 1 9 1 3z"/></svg>555-210-4471</li>
        <li><svg viewBox="0 0 16 16"><path d="M4 0h8v16H4zM5.5 2v10h5V2z"/></svg>555-318-2094</li>
        <li><svg viewBox="0 0 16 16"><path d="M1 5h14v9H1zM4 1h8v3H4z"/></svg>555-476-1382</li>
        <li><svg viewBox="0 0 16 16"><path d="M1 3h14v10H1zM2 4l6 5 6-5z"/></svg>hello@ternisusmile.com</li>
        <li><svg viewBox="0 0 16 16"><circle cx="8" cy="8" r="7"/></svg>www.ternisusmile.com</li>
      </ul>
    </div>
  </section>

  <section class="card card--back">
    <div class="brand">
      <span class="brand__square"></span>
      <span class="brand__name">dr Ternisu</span>
    </div>
  </section>
</body>
</html>
```